QP Fiduciary Website Redesign Contest

We want to refresh our website to be more insitutional, professional for an international audience. We have designed a new logo for this purpose and that has been attached. A full brand brief and positioning statement has also been attached. Please read through all the documents carefully before designing. The old website is found here: https://qp-fiduciary.example/

Target Market(s)

Actuaries and associated businesses internationally

Industry/Entity Type

professional services - actuaries

Number of Pages Required

3 page

Font styles to use
Sans Serif

Colors
0054AA
0677BA
7BADD7
CADEEF
E8F1F8
0094D4
00A9DD
6FCCEA
C7EBF8
E9F6FB
F0912C
F2A743
F7CA91
FBE8D2
FDF5EE
EE7325
F08F49
F5BC92
FAE3D3
FDF4ED
EB3D1F
EC4F4E
F09395
F8D3D4
FCEDEE

Requirements
Must have
• blues and greens to match the logo color, complimentary colors, navigation
Nice to have
• old site: https://qp-fiduciary.example/

```html
<!DOCTYPE html>
<html lang="en">
<head>
<meta charset="utf-8">
<title>QP Fiduciary — Actuarial Software</title>
<link href="https://fonts.googleapis.com/css2?family=Cinzel:wght@600;700&family=Open+Sans:wght@400;600;700&display=swap" rel="stylesheet">
<style>
:root{
  --navy:#0d2446;
  --blue:#0054AA;
  --blue-mid:#0677BA;
  --blue-soft:#7BADD7;
  --blue-pale:#E8F1F8;
  --orange:#EE7325;
  --orange-soft:#F08F49;
  --ink:#1c2433;
  --text:#4a5466;
  --white:#ffffff;
}
*{box-sizing:border-box;margin:0;padding:0}
html,body{width:1200px;height:3924px;overflow:hidden;background:var(--white)}
body{font-family:"Open Sans",Arial,sans-serif;color:var(--text);position:relative}
.serif{font-family:"Cinzel",Georgia,serif}
a{color:inherit;text-decoration:none}

.site-header{position:absolute;top:0;left:0;width:1200px;height:88px;display:flex;align-items:center;justify-content:space-between;padding:0 40px 0 48px}
.brand{display:flex;align-items:center;gap:10px;font-weight:700;font-size:26px;color:var(--navy);letter-spacing:1px}
.brand-dot{width:22px;height:22px;border-radius:50%;background:var(--orange)}
.main-nav{display:flex;gap:38px;font-size:15px;font-weight:600;color:var(--navy);letter-spacing:.5px}
.main-nav a.active{color:var(--orange);border-bottom:2px solid var(--orange);padding-bottom:4px}

.hero{position:absolute;top:100px;left:40px;width:1120px;height:572px;border-radius:14px;overflow:hidden;
  background:linear-gradient(180deg,#5c8fb6 0%,#2f5f8c 45%,#1a3a60 100%)}
.hero-copy{position:absolute;top:200px;left:0;width:100%;text-align:center;color:var(--white)}
.hero h1{font-size:40px;line-height:52px;font-weight:700;letter-spacing:1px}
.hero p{font-size:17px;line-height:26px;margin:20px auto 0;width:620px}
.btn{display:inline-flex;align-items:center;gap:10px;background:var(--orange);color:var(--white);font-size:15px;font-weight:600;padding:13px 26px;border-radius:6px}
.hero .btn{margin-top:34px}

.section-title{font-size:30px;font-weight:700;color:var(--ink);letter-spacing:1px}

.platform{position:absolute;top:770px;left:112px;width:976px}
.platform p{font-size:16px;line-height:27px;margin-top:20px}
.platform .btn{margin-top:36px}

.steps{position:absolute;top:1112px;left:208px;display:flex;gap:28px}
.step{width:176px;height:176px;border-radius:10px;border:2px solid transparent;
  background:linear-gradient(#fff,#fff) padding-box,linear-gradient(90deg,var(--blue-soft),var(--orange-soft)) border-box;
  display:flex;flex-direction:column;align-items:center;justify-content:center;gap:22px;box-shadow:0 6px 16px rgba(13,36,70,.08)}
.step span{font-size:15px;font-weight:700;color:var(--navy);letter-spacing:1px}

.centered{position:absolute;left:0;width:1200px;text-align:center}
.capabilities-title{top:1386px}
.capabilities{position:absolute;top:1480px;left:112px;display:flex;gap:32px}
.cap-card{width:304px;height:280px;border-radius:10px;border:2px solid transparent;
  background:linear-gradient(#fff,#fff) padding-box,linear-gradient(90deg,var(--blue-soft),var(--orange-soft)) border-box;
  text-align:center;padding:40px 30px 0;box-shadow:0 6px 16px rgba(13,36,70,.08)}
.cap-card.featured{background:linear-gradient(160deg,#1c5fa8,#0d2d5e);border:none;color:var(--white)}
.cap-card h3{font-family:"Cinzel",Georgia,serif;font-size:18px;color:var(--navy);margin:22px 0 12px}
.cap-card.featured h3{color:var(--white)}
.cap-card p{font-size:14px;line-height:21px}
.cap-icon{width:64px;height:64px;border-radius:50%;margin:0 auto;display:flex;align-items:center;justify-content:center;border:2px solid var(--blue-soft)}
.featured .cap-icon{border-color:rgba(255,255,255,.6)}

.insights-title{top:1898px}
.insights{position:absolute;top:2032px;left:132px;display:flex;gap:40px}
.insight{width:448px;height:480px;border-radius:10px;box-shadow:0 8px 22px rgba(13,36,70,.12);overflow:hidden;background:#fff}
.insight-media{height:240px}
.insight-body{padding:24px 26px}
.insight h3{font-family:"Cinzel",Georgia,serif;font-size:18px;line-height:24px;color:var(--navy)}
.insight p{font-size:14px;line-height:21px;margin:12px 0 18px}
.insight .btn{font-size:13px;padding:10px 18px}
.arrow{position:absolute;top:2240px;width:40px;height:40px;border-radius:50%;border:1.5px solid #8a94a6;display:flex;align-items:center;justify-content:center}

.gov-title{top:2640px;line-height:44px}
.features{position:absolute;top:2788px;left:120px;display:grid;grid-template-columns:460px 460px;column-gap:48px;row-gap:68px}
.feature{height:92px;border-radius:8px;border:2px solid transparent;
  background:linear-gradient(#fff,#fff) padding-box,linear-gradient(90deg,var(--blue-soft),var(--orange-soft)) border-box;
  display:flex;align-items:center;gap:20px;padding:0 24px;box-shadow:0 6px 16px rgba(13,36,70,.07)}
.feature-icon{flex:none;width:48px;height:48px;border-radius:50%;background:var(--blue-pale);display:flex;align-items:center;justify-content:center}
.feature p{font-size:14px;line-height:20px;color:var(--ink)}

.cta{position:absolute;top:3180px;left:0;width:1200px;height:332px;background:linear-gradient(120deg,#0a1834,#133a6c 60%,#0a1834);text-align:center;color:var(--white);padding-top:112px}
.cta h2{font-size:30px;font-weight:700;letter-spacing:1px}
.cta p{font-size:16px;line-height:24px;width:680px;margin:16px auto 0}
.cta .btn{margin-top:28px}

.site-footer{position:absolute;top:3512px;left:0;width:1200px;height:412px}
.footer-brand{position:absolute;top:110px;left:120px}
.social{position:absolute;top:180px;left:120px;display:flex;gap:10px}
.social span{width:28px;height:28px;border-radius:50%;background:var(--orange)}
.footer-col{position:absolute;top:112px;font-size:14px;line-height:24px;color:var(--ink)}
.footer-col h4{font-size:15px;font-weight:700;letter-spacing:1px;margin-bottom:8px;color:var(--navy)}
.footer-rule{position:absolute;top:364px;left:120px;width:960px;height:1px;background:#d6dbe3}
.copyright{position:absolute;top:380px;left:120px;font-size:12px;color:#6b7486}
</style>
</head>
<body>

<header class="site-header">
  <a class="brand" href="https://qp-fiduciary.example/"><span class="brand-dot"></span>QP FIDUCIARY</a>
  <nav class="main-nav">
    <a class="active" href="#">HOME</a><a href="#">PLATFORM</a><a href="#">SOLUTIONS</a><a href="#">INSIGHTS</a><a href="#">COMPANY</a><a href="#">CONTACT</a>
  </nav>
</header>

<section class="hero" role="img" aria-label="Photograph of a modern financial district skyline under a blue sky">
  <div class="hero-copy">
    <h1 class="serif">ACTUARIAL SOFTWARE FOR STRUCTURED,<br>AUDITABLE FINANCIAL ANALYSIS</h1>
    <p>Software that translates actuarial methodologies into disciplined, decision-ready analytical tools across diverse regulatory environments.</p>
    <a class="btn" href="#">Request a Technical Walkthrough <span>→</span></a>
  </div>
</section>

<section class="platform">
  <h2 class="section-title serif">A DISCIPLINED PLATFORM FOR ACTUARIAL ANALYSIS</h2>
  <p>QP Fiduciary provides modular actuarial software designed to support structured reserving, pricing, and risk analysis workflows. The platform enables actuarial teams to move beyond fragmented spreadsheets by introducing consistent analytical structure, transparent assumptions, and governance-ready outputs suitable for regulated environments. Rather than replacing actuarial judgment, the platform supports it through clear methodologies, structured workflows, and defensible analytical processes.</p>
  <a class="btn" href="#">Explore the Platform <span>→</span></a>
</section>

<div class="steps">
  <div class="step"><svg width="56" height="56" viewBox="0 0 56 56" fill="none" stroke="#0d2446" stroke-width="2.5"><rect x="8" y="10" width="34" height="38" rx="2"/><path d="M16 22h18M16 30h18M16 38h10"/><path d="M36 40l12-12" stroke="#EE7325"/></svg><span>INPUT</span></div>
  <div class="step"><svg width="56" height="56" viewBox="0 0 56 56" fill="none" stroke="#0d2446" stroke-width="2.5"><path d="M8 48h42"/><rect x="12" y="32" width="7" height="14"/><rect x="24" y="24" width="7" height="22"/><rect x="36" y="16" width="7" height="30"/><path d="M10 24l12-10 10 6 14-12" stroke="#EE7325"/></svg><span>ANALYSIS</span></div>
  <div class="step"><svg width="56" height="56" viewBox="0 0 56 56" fill="none" stroke="#0d2446" stroke-width="2.5"><rect x="6" y="8" width="44" height="36" rx="4"/><circle cx="17" cy="20" r="4"/><circle cx="28" cy="20" r="4"/><circle cx="39" cy="20" r="4" stroke="#EE7325"/><path d="M14 34h28"/></svg><span>REVIEW</span></div>
  <div class="step"><svg width="56" height="56" viewBox="0 0 56 56" fill="none" stroke="#0d2446" stroke-width="2.5"><rect x="10" y="8" width="30" height="40" rx="2"/><path d="M18 20h14M18 28h14"/><path d="M36 36l8 8m0 0l8-8m-8 8V28" stroke="#EE7325"/></svg><span>OUTPUT</span></div>
</div>

<h2 class="centered section-title serif capabilities-title">CORE ANALYTICAL CAPABILITIES</h2>
<div class="capabilities">
  <div class="cap-card featured">
    <div class="cap-icon"><svg width="32" height="32" viewBox="0 0 32 32" fill="none" stroke="#fff" stroke-width="2"><ellipse cx="16" cy="9" rx="10" ry="4"/><path d="M6 9v14c0 2 4.5 4 10 4s10-2 10-4V9M6 16c0 2 4.5 4 10 4s10-2 10-4"/></svg></div>
    <h3>RESERVING &amp; VALUATION</h3>
    <p>Software supporting structured reserving workflows and financial reporting across jurisdictions.</p>
  </div>
  <div class="cap-card">
    <div class="cap-icon"><svg width="32" height="32" viewBox="0 0 32 32" fill="none" stroke="#0d2446" stroke-width="2"><circle cx="16" cy="16" r="11"/><path d="M20 11h-5a3 3 0 000 6h2a3 3 0 010 6h-5M16 8v16" stroke="#EE7325"/></svg></div>
    <h3>PRICING</h3>
    <p>Models supporting insurance and reinsurance pricing based on actuarial methodologies.</p>
  </div>
  <div class="cap-card">
    <div class="cap-icon"><svg width="32" height="32" viewBox="0 0 32 32" fill="none" stroke="#0d2446" stroke-width="2"><rect x="6" y="4" width="20" height="24" rx="2"/><path d="M11 22v-4M16 22v-8M21 22v-11" stroke="#EE7325"/></svg></div>
    <h3>ENTERPRISE RISK MANAGEMENT</h3>
    <p>Software supporting enterprise risk optimization and capital modeling.</p>
  </div>
</div>

<h2 class="centered section-title serif insights-title">OUR INSIGHTS</h2>
<a class="arrow" style="left:40px" href="#"><svg width="14" height="14" viewBox="0 0 14 14" fill="none" stroke="#4a5466" stroke-width="2"><path d="M9 2L4 7l5 5"/></svg></a>
<a class="arrow" style="left:1120px" href="#"><svg width="14" height="14" viewBox="0 0 14 14" fill="none" stroke="#4a5466" stroke-width="2"><path d="M5 2l5 5-5 5"/></svg></a>
<div class="insights">
  <article class="insight">
    <div class="insight-media" role="img" aria-label="Photograph of stacked coins beside a small savings jar" style="background:linear-gradient(135deg,#cfd8e2,#8c9fb3 60%,#5b6f86)"></div>
    <div class="insight-body">
      <h3>METHODOLOGICAL PERSPECTIVES IN ACTUARIAL RESERVING</h3>
      <p>An examination of structured approaches to reserving analysis, including methodological transparency, assumption governance, and comparative scenario evaluation.</p>
      <a class="btn" href="#">Read Insights <span>→</span></a>
    </div>
  </article>
  <article class="insight">
    <div class="insight-media" role="img" aria-label="Photograph of a printed financial bar chart report" style="background:linear-gradient(135deg,#eef4fa,#a9c8e4 55%,#3d79b4)"></div>
    <div class="insight-body">
      <h3>OBSERVATIONS ON ACTUARIAL PRACTICE IN EMERGING MARKETS</h3>
      <p>Practical reflections on actuarial analysis in developing insurance markets, where regulatory structures and data availability continue to evolve.</p>
      <a class="btn" href="#">Read Insights <span>→</span></a>
    </div>
  </article>
</div>

<h2 class="centered section-title serif gov-title">DESIGNED FOR GOVERNANCE, TRANSPARENCY, AND<br>ANALYTICAL DISCIPLINE</h2>
<div class="features">
  <div class="feature"><div class="feature-icon"><svg width="24" height="24" viewBox="0 0 24 24" fill="none" stroke="#0054AA" stroke-width="2"><rect x="4" y="3" width="16" height="18" rx="2"/><path d="M8 12l3 3 5-6" stroke="#EE7325"/></svg></div><p>Structured workflows suitable for multi-jurisdictional actuarial review</p></div>
  <div class="feature"><div class="feature-icon"><svg width="24" height="24" viewBox="0 0 24 24" fill="none" stroke="#0054AA" stroke-width="2"><path d="M3 20h18M6 16v-4M11 16V8M16 16v-6"/><path d="M4 9l6-5 5 3 5-4" stroke="#EE7325"/></svg></div><p>Comparative scenario analysis across portfolios and time periods</p></div>
  <div class="feature"><div class="feature-icon"><svg width="24" height="24" viewBox="0 0 24 24" fill="none" stroke="#0054AA" stroke-width="2"><circle cx="11" cy="11" r="6"/><path d="M16 16l5 5" stroke="#EE7325"/></svg></div><p>Transparent assumptions and methodological clarity</p></div>
  <div class="feature"><div class="feature-icon"><svg width="24" height="24" viewBox="0 0 24 24" fill="none" stroke="#0054AA" stroke-width="2"><path d="M12 3l8 3v6c0 5-4 8-8 9-4-1-8-4-8-9V6z"/><path d="M8 12l3 3 5-5" stroke="#EE7325"/></svg></div><p>Outputs designed to support professional scrutiny and governance review</p></div>
</div>

<section class="cta">
  <h2 class="serif">INTERESTED IN EXPLORING THE PLATFORM?</h2>
  <p>Request a technical walkthrough to see how QP Fiduciary supports structured actuarial analysis and governance-ready decision making.</p>
  <a class="btn" href="#">Request a Technical Walkthrough <span>→</span></a>
</section>

<footer class="site-footer">
  <a class="brand footer-brand" href="https://qp-fiduciary.example/"><span class="brand-dot"></span>QP FIDUCIARY</a>
  <div class="social"><span></span><span></span><span></span></div>
  <div class="footer-col" style="left:432px"><h4>PLATFORM</h4><div>Platform Overview</div><div>Reserving &amp; Valuation</div><div>Pricing</div><div>Enterprise Risk Management</div></div>
  <div class="footer-col" style="left:688px"><h4>COMPANY</h4><div>About QP Fiduciary</div><div>Our Approach</div><div>Contact</div></div>
  <div class="footer-col" style="left:888px"><h4>INSIGHTS</h4><div>Latest Insights</div><div>Research Notes</div><div>Methodology Perspectives</div></div>
  <div class="footer-rule"></div>
  <div class="copyright">© 2026 QP Fiduciary. All rights reserved.</div>
</footer>

</body>
</html>
```